Professional and creative business card design for recruiting service providers

Our company supports German medium-sized companies in filling vacancies promptly. For this we use social media marketing and bring our customers into the visibility.

We want a professional but also creative design for our business cards.

Please look at lindqvar-staff.de to get an impression of our CI.

Target Market(s)

Small and medium-sized companies in Germany from the industry

Industry/Entity Type

Industrie, Handwerk

Contact Information for Business Card

Name, Position, Telefonnummer, Email, Website

Colors
EE7325
F08F49
F5BC92
FAE3D3
FDF4ED

Requirements
Must have
• A picture of the employee and in the style of www.lindqvar-staff.de

```html
<!DOCTYPE html>
<html lang="de">
<head>
<meta charset="utf-8">
<title>Lindqvar &amp; Staff – Visitenkarte</title>
<link rel="stylesheet" href="https://fonts.googleapis.com/css2?family=Montserrat:wght@700;800&family=Arimo:wght@400;700&display=swap">
<style>
  :root{
    --stage:#2b231f;
    --card:#333333;
    --card-emboss:#3e3e3e;
    --orange:#f0602a;
    --white:#ffffff;
    --photo-top:#3a3a3a;
    --photo-bottom:#1e1e22;
  }
  *{margin:0;padding:0;box-sizing:border-box}
  html,body{width:1200px;height:716px;overflow:hidden;background:var(--stage)}
  .stage{position:relative;width:1200px;height:716px;display:flex;align-items:center;justify-content:center;gap:50px}
  .card{position:relative;width:520px;height:336px;background:var(--card);overflow:hidden;box-shadow:0 12px 30px rgba(0,0,0,.45)}

  /* back side */
  .card-back{display:flex;align-items:center;justify-content:center}
  .brand-emboss{font-family:"Montserrat",sans-serif;font-weight:800;font-size:40px;line-height:1.05;letter-spacing:3px;color:var(--card-emboss);text-transform:uppercase;display:flex;align-items:center;gap:22px}
  .brand-emboss .mark{width:70px;height:70px;background:var(--card-emboss)}

  /* front side */
  .portrait{position:absolute;left:0;bottom:0;width:270px;height:300px;background:linear-gradient(180deg,var(--photo-top),var(--photo-bottom))}
  .address-band{position:absolute;left:270px;right:0;bottom:0;height:74px;background:var(--orange)}
  .info{position:absolute;right:26px;top:30px;text-align:right;color:var(--white);font-family:"Arimo",sans-serif}
  .brand{display:flex;align-items:center;justify-content:flex-end;gap:14px;font-family:"Montserrat",sans-serif;font-weight:800;font-size:24px;line-height:1.05;letter-spacing:2px;text-transform:uppercase;text-align:left;color:var(--white)}
  .brand .mark{width:46px;height:46px;background:var(--orange)}
  .person{margin-top:26px}
  .person-name{font-family:"Arimo",sans-serif;font-weight:700;font-size:19px;letter-spacing:.5px;color:var(--orange);text-transform:uppercase}
  .person-role{font-size:16px;margin-top:2px}
  .contacts{list-style:none;margin-top:16px;font-size:14px;line-height:1.45}
  .contacts li{display:flex;align-items:center;justify-content:flex-end;gap:8px}
  .contacts svg{width:13px;height:13px;flex:none}
  .address{position:absolute;right:26px;bottom:14px;text-align:right;color:var(--white);font-family:"Arimo",sans-serif;font-size:15px;line-height:1.35}
</style>
</head>
<body>
<main class="stage">
  <section class="card card-back" aria-label="Rückseite">
    <div class="brand-emboss"><span class="mark"></span><span>Lindqvar<br>&amp; Staff</span></div>
  </section>

  <section class="card card-front" aria-label="Vorderseite">
    <div class="portrait" role="img" aria-label="Porträtfoto des Mitarbeiters"></div>
    <div class="address-band"></div>

    <div class="info">
      <div class="brand"><span class="mark"></span><span>Lindqvar<br>&amp; Staff</span></div>
      <div class="person">
        <div class="person-name">Lukas Brenner</div>
        <div class="person-role">Manager</div>
      </div>
      <ul class="contacts">
        <li>0171 204 3917
          <svg viewBox="0 0 24 24" aria-hidden="true"><path fill="var(--orange)" d="M6.6 10.8a15 15 0 0 0 6.6 6.6l2.2-2.2c.3-.3.7-.4 1-.2 1.1.4 2.3.6 3.6.6.6 0 1 .4 1 1V20c0 .6-.4 1-1 1A17 17 0 0 1 3 4c0-.6.4-1 1-1h3.5c.6 0 1 .4 1 1 0 1.3.2 2.5.6 3.6.1.3 0 .7-.2 1z"/></svg>
        </li>
        <li>info@lindqvar-staff.de
          <svg viewBox="0 0 24 24" aria-hidden="true"><rect x="2.5" y="5" width="19" height="14" fill="none" stroke="var(--orange)" stroke-width="2"/><path d="M3 6l9 7 9-7" fill="none" stroke="var(--orange)" stroke-width="2"/></svg>
        </li>
        <li>www.lindqvar-staff.de
          <svg viewBox="0 0 24 24" aria-hidden="true"><g fill="none" stroke="var(--orange)" stroke-width="2"><circle cx="12" cy="12" r="9.5"/><ellipse cx="12" cy="12" rx="4" ry="9.5"/><path d="M2.5 12h19M4 7h16M4 17h16"/></g></svg>
        </li>
      </ul>
    </div>

    <address class="address">Kastanienweg 27a<br>70174 Stuttgart</address>
  </section>
</main>
</body>
</html>
```